New business card/stationary for a consulting company

I am looking for a clean and very professional looking business card for my consulting company as well as corresponding stationary. I am uploading our logo. I like simple and powerful for the feel. No graphics but I am open on everything else. Below is my contact information but would like the final to be in a version I can add my employees information into and print. Thank you.

Daniel Whitcombe
dan@ferncliffadvisory.com
2870 North 9th Avenue, Summit Floor, Elm Ridge, Illinois 60531
www.ferncliffadvisory.com

Industry/Entity Type

Consulting

Contact Information for Business Card

Daniel Whitcombe
dan@ferncliffadvisory.com
www.ferncliffadvisory.com

Font styles to use
Serif
Sans Serif

Requirements
Must have
• Our logo and the business card details.
Nice to have
• our website www.ferncliffadvisory.com

```html
<!DOCTYPE html>
<html lang="en">
<head>
<meta charset="utf-8">
<title>Ferncliff Advisory — Business Card</title>
<link rel="stylesheet" href="https://fonts.googleapis.com/css2?family=Questrial&family=Crimson+Text:ital,wght@0,400;0,700;1,400&display=swap">
<style>
  :root {
    --ink-blue: #0a0a9a;
    --deep-blue: #06066e;
    --paper: #f1f1f1;
    --strip: #e6e6e6;
    --text-dark: #1c1c1c;
    --stage: #dcdde2;
    --white: #ffffff;
  }
  * { box-sizing: border-box; margin: 0; padding: 0; }
  html, body { width: 1200px; height: 900px; overflow: hidden; }
  body {
    background: var(--stage);
    position: relative;
    font-family: "Crimson Text", Georgia, serif;
  }
  .card {
    position: absolute;
    left: 250px;
    width: 700px;
    height: 400px;
    overflow: hidden;
    box-shadow: 0 10px 30px rgba(0,0,0,0.18);
  }

  /* Back side */
  .card-back {
    top: 40px;
    background: radial-gradient(ellipse at 30% 30%, #1010b8 0%, var(--ink-blue) 45%, var(--deep-blue) 100%);
    color: var(--white);
  }
  .back-mark {
    position: absolute;
    right: 90px;
    top: 92px;
    width: 64px;
    height: 64px;
    background: var(--strip);
  }
  .back-name {
    position: absolute;
    right: 60px;
    top: 172px;
    font-family: "Questrial", Arial, sans-serif;
    font-size: 50px;
    letter-spacing: 3px;
    color: var(--strip);
    white-space: nowrap;
  }
  .back-rule {
    position: absolute;
    left: 0;
    top: 276px;
    width: 400px;
    height: 2px;
    background: var(--strip);
  }
  .back-web {
    position: absolute;
    left: 414px;
    top: 262px;
    font-size: 21px;
    color: var(--strip);
    letter-spacing: 0.3px;
  }

  /* Front side */
  .card-front {
    top: 470px;
    background: var(--paper);
  }
  .front-strip {
    position: absolute;
    left: 0; top: 0;
    width: 92px; height: 100%;
    background: var(--strip);
  }
  .front-band {
    position: absolute;
    left: 92px; top: 0;
    width: 170px; height: 100%;
    background: var(--ink-blue);
  }
  .band-logo {
    position: absolute;
    left: 50%; top: 50%;
    transform: translate(-50%, -50%) rotate(-90deg);
    display: flex;
    align-items: center;
    gap: 14px;
    white-space: nowrap;
  }
  .band-logo .mark {
    width: 34px; height: 34px;
    background: var(--strip);
  }
  .band-logo .name {
    font-family: "Questrial", Arial, sans-serif;
    font-size: 30px;
    letter-spacing: 2px;
    color: var(--strip);
  }
  .front-rule {
    position: absolute;
    left: 440px; top: 0;
    width: 2px; height: 128px;
    background: var(--ink-blue);
  }
  .contact {
    position: absolute;
    left: 300px;
    top: 165px;
  }
  .contact-name {
    font-size: 26px;
    font-weight: 700;
    letter-spacing: 0.5px;
    color: var(--ink-blue);
    text-transform: uppercase;
    margin-bottom: 14px;
    margin-left: 40px;
  }
  .contact-list { list-style: none; }
  .contact-list li {
    display: flex;
    align-items: flex-start;
    gap: 12px;
    font-size: 18px;
    line-height: 24px;
    color: var(--text-dark);
    margin-bottom: 4px;
  }
  .contact-list svg { flex: none; margin-top: 2px; }
</style>
</head>
<body>

<section class="card card-back" aria-label="Business card back">
  <div class="back-mark"></div>
  <div class="back-name">FERNCLIFF ADVISORY</div>
  <div class="back-rule"></div>
  <div class="back-web">www.ferncliffadvisory.com</div>
</section>

<section class="card card-front" aria-label="Business card front">
  <div class="front-strip"></div>
  <div class="front-band">
    <div class="band-logo">
      <span class="mark"></span>
      <span class="name">FERNCLIFF ADVISORY</span>
    </div>
  </div>
  <div class="front-rule"></div>

  <div class="contact">
    <h1 class="contact-name">Daniel Whitcombe</h1>
    <ul class="contact-list">
      <li>
        <svg width="24" height="20" viewBox="0 0 24 20" aria-hidden="true">
          <rect width="24" height="20" fill="var(--ink-blue)"/>
          <rect x="5" y="5" width="14" height="10" fill="none" stroke="#fff" stroke-width="1.5"/>
          <path d="M5 5 L12 11 L19 5" fill="none" stroke="#fff" stroke-width="1.5"/>
        </svg>
        <span>dan@ferncliffadvisory.com</span>
      </li>
      <li>
        <svg width="24" height="20" viewBox="0 0 24 20" aria-hidden="true">
          <rect width="24" height="20" fill="var(--ink-blue)"/>
          <circle cx="12" cy="10" r="6" fill="none" stroke="#fff" stroke-width="1.5"/>
          <path d="M6 10 H18 M12 4 C9 7 9 13 12 16 C15 13 15 7 12 4" fill="none" stroke="#fff" stroke-width="1.2"/>
        </svg>
        <span>www.ferncliffadvisory.com</span>
      </li>
      <li>
        <svg width="24" height="20" viewBox="0 0 24 20" aria-hidden="true">
          <rect width="24" height="20" fill="var(--ink-blue)"/>
          <path d="M12 16 C8 11 7 9 7 8 A5 5 0 0 1 17 8 C17 9 16 11 12 16 Z" fill="#fff"/>
          <circle cx="12" cy="8" r="2" fill="var(--ink-blue)"/>
        </svg>
        <span>2870 North 9th Avenue, Summit Floor,<br>Elm Ridge, Illinois 60531</span>
      </li>
    </ul>
  </div>
</section>

</body>
</html>
```